R7M Horizon Business Card Design

We need a business card created for our New Business "R7M Horizon"<br/><br/>The business card design is up to you however the following information must be on the business card:<br/><br/>Front of the business card -<br/>Email :darrenk@r7mhorizon.nz<br/>Mobile: +64 (0) 22 4870 619<br/>Website: www.r7mhorizon.nz<br/>Card Owner Name: Darren Kestrow<br/>Company Title: Business Development Manager<br/>Slogan: "The EDGE of new ground". <br/>Logo On the front attached to the design brief<br/><br/>On the back: <br/>Space on the back for 4 more versions of the logo across the bottom of the card indicating different subsidiary brands - R7M Coffee, R7M Arts, R7M ?? (The card will be used for all of these brands - We Will add the extra subsidiary logos to the design once the design is finished (We are a graphics design team). <br/><br/>Other than that we want a premium feeling logo that remains universally usable depending on the business entity that we are using the card for. The use of bright bold colours would be great but we still want the card to feel premium.
Target Market(s)
Gift Design and Manufacturing Companies
Contact Information for Business Card
Front of the business card -
Email :darrenk@r7mhorizon.nz
Mobile: +64 (0) 22 4870 619
Website: www.r7mhorizon.nz
Card Owner Name: Darren Kestrow
Company Title: Business Development Manager
Slogan: "The EDGE of new ground".
Logo On the front attached to the design brief

```html
<!DOCTYPE html>
<html lang="en">
<head>
<meta charset="utf-8">
<title>R7M Horizon Business Card</title>
<link rel="stylesheet" href="https://fonts.googleapis.com/css2?family=Orbitron:wght@800&family=Open+Sans:ital,wght@0,400;0,600;1,400;1,700&display=swap">
<style>
  :root {
    --brand-blue: #2e3e9e;
    --brand-blue-deep: #24307f;
    --name-blue: #2a3aa8;
    --ink-grey: #4a4a4a;
    --card-white: #ffffff;
    --card-white-soft: #f1f1f3;
    --logo-silver: #d6d9e6;
    --stage: #e4e5ea;
  }
  * { box-sizing: border-box; margin: 0; padding: 0; }
  html, body { width: 1200px; height: 900px; overflow: hidden; }
  body {
    background: var(--stage);
    font-family: "Open Sans", Arial, sans-serif;
    position: relative;
  }
  .card {
    position: absolute;
    left: 250px;
    width: 700px;
    height: 400px;
    box-shadow: 0 6px 18px rgba(0,0,0,0.18);
    overflow: hidden;
  }
  /* Front */
  .card-front {
    top: 40px;
    background: radial-gradient(ellipse at 55% 35%, var(--card-white) 40%, var(--card-white-soft) 100%);
  }
  .identity {
    position: absolute;
    left: 42px;
    top: 128px;
  }
  .identity-name {
    font-family: "Orbitron", "Arial Black", sans-serif;
    font-weight: 800;
    font-size: 28px;
    letter-spacing: 1px;
    color: var(--name-blue);
    text-transform: uppercase;
    line-height: 1.1;
    white-space: nowrap;
  }
  .identity-role {
    font-size: 17px;
    color: var(--ink-grey);
    margin-top: 4px;
  }
  .divider {
    position: absolute;
    left: 400px;
    top: 138px;
    width: 2px;
    height: 82px;
    background: var(--name-blue);
  }
  .contact-list {
    position: absolute;
    left: 420px;
    top: 144px;
    list-style: none;
  }
  .contact-item {
    display: flex;
    align-items: center;
    gap: 10px;
    font-size: 17px;
    color: var(--ink-grey);
    line-height: 25px;
    white-space: nowrap;
  }
  .contact-icon { width: 14px; height: 14px; flex: none; }
  .slogan-band {
    position: absolute;
    left: 0;
    bottom: 0;
    width: 100%;
    height: 66px;
    background: var(--brand-blue);
    display: flex;
    align-items: center;
    padding-left: 42px;
  }
  .slogan {
    color: var(--card-white);
    font-style: italic;
    font-size: 19px;
  }
  .slogan strong { font-weight: 700; }
  /* Back */
  .card-back {
    top: 470px;
    background: radial-gradient(ellipse at 40% 30%, var(--brand-blue) 30%, var(--brand-blue-deep) 100%);
    display: flex;
    flex-direction: column;
    align-items: center;
    justify-content: center;
    gap: 30px;
  }
  .brand-name {
    font-size: 50px;
    font-weight: 600;
    color: var(--logo-silver);
    letter-spacing: 1px;
  }
  .back-url {
    font-size: 19px;
    color: var(--logo-silver);
    letter-spacing: 1px;
  }
</style>
</head>
<body>
  <section class="card card-front">
    <div class="identity">
      <h1 class="identity-name">Darren Kestrow</h1>
      <p class="identity-role">Business Development Manager</p>
    </div>
    <div class="divider"></div>
    <ul class="contact-list">
      <li class="contact-item">
        <svg class="contact-icon" viewBox="0 0 16 16"><path d="M4 1.5 6.2 5 4.8 6.4c.9 2 2.5 3.6 4.6 4.6L10.8 9.6 14.5 12l-1.3 2.3C7.5 14 2 8.5 1.7 2.8Z" fill="#2a3aa8"/></svg>
        <span>+64 (0) 22 4870 619</span>
      </li>
      <li class="contact-item">
        <svg class="contact-icon" viewBox="0 0 16 16"><rect x="1.5" y="3.5" width="13" height="9" fill="none" stroke="#2a3aa8" stroke-width="1.4"/><path d="M1.5 3.5 8 9l6.5-5.5" fill="none" stroke="#2a3aa8" stroke-width="1.4"/></svg>
        <span>darrenk@r7mhorizon.nz</span>
      </li>
      <li class="contact-item">
        <svg class="contact-icon" viewBox="0 0 16 16"><circle cx="8" cy="8" r="6.5" fill="#2a3aa8"/><path d="M1.5 8h13M8 1.5v13M3 4.5h10M3 11.5h10" stroke="#fff" stroke-width="0.8" fill="none"/><ellipse cx="8" cy="8" rx="3" ry="6.5" fill="none" stroke="#fff" stroke-width="0.8"/></svg>
        <span>www.r7mhorizon.nz</span>
      </li>
    </ul>
    <div class="slogan-band">
      <p class="slogan">The <strong>EDGE</strong> of new ground</p>
    </div>
  </section>

  <section class="card card-back">
    <span class="brand-name">R7M Horizon</span>
    <p class="back-url">www.r7mhorizon.nz</p>
  </section>
</body>
</html>
```